Lawn sign for construction company

Would like this to be a very clean and high end design for luxury homes. We need a yard sign designed that includes the company logo, website, phone number and major service offerings (residential and commercial renovations and maintenance)
The company website is brackwellbuilders.com all other contact info is in the attachments
Target Market(s)
Luxury home owners and business owners
Industry/Entity Type
Construction/Home Improvement
Font styles to use
Other font styles liked:
- See company logo and other graphics included for title text fonts. All other fonts can be standard sans serif.
Colors
0054AA
0677BA
7BADD7
CADEEF
E8F1F8
Requirements
Must have
- Clean, easy to read design, would like 2 sided sign. A main sign side and back side which states “free estimates, and includes the website and phone number. Must also match the color scheme of the provided logo and other company images. Dark Navy blue primary color, gray secondary color, and orange as an accent color.
Nice to have
- 2nd sign side very simple design
Should not have
- Too many graphics limit to 1-3 colors

```html
<!DOCTYPE html>
<html lang="en">
<head>
<meta charset="utf-8">
<title>Brackwell Builders – Yard Sign, Front and Back</title>
<link href="https://fonts.googleapis.com/css2?family=Poppins:wght@300;400;600;700&family=Roboto:wght@400;500&display=swap" rel="stylesheet">
<style>
  :root {
    --navy: #1e1b5a;
    --navy-ink: #1f1d5c;
    --orange: #c96f2a;
    --orange-bright: #e8842a;
    --silver: #b9bcc4;
    --gray: #6d6e72;
    --white: #ffffff;
    --page: #eef0f3;
  }
  * { box-sizing: border-box; margin: 0; padding: 0; }
  html, body { width: 815px; height: 1200px; overflow: hidden; }
  body {
    background: var(--page);
    font-family: "Poppins", Arial, sans-serif;
    display: flex;
    flex-direction: column;
    align-items: center;
    justify-content: center;
    gap: 60px;
  }
  .sign {
    position: relative;
    width: 720px;
    height: 500px;
    box-shadow: 0 6px 18px rgba(0,0,0,.18);
  }
  .sign__frame-outer, .sign__frame-inner {
    position: absolute;
    pointer-events: none;
  }

  /* Front side */
  .sign--front { background: var(--navy); }
  .sign--front .sign__frame-outer { inset: 26px; border: 3px solid var(--silver); }
  .sign--front .sign__frame-inner { inset: 38px; border: 1px solid var(--silver); }
  .brand-lockup {
    position: absolute;
    top: 40px;
    height: 330px;
    left: 0; right: 0;
    display: flex;
    align-items: center;
    justify-content: center;
    gap: 26px;
  }
  .brand-lockup__dot {
    width: 120px; height: 120px;
    border-radius: 50%;
    background: var(--gray);
    flex: none;
  }
  .brand-lockup__name {
    font-family: "Poppins", Arial, sans-serif;
    font-weight: 700;
    font-size: 56px;
    line-height: 1.02;
    letter-spacing: 1px;
    color: var(--orange-bright);
  }
  .front-rule {
    position: absolute;
    left: 90px; right: 130px;
    top: 372px;
    height: 2px;
    background: linear-gradient(90deg, transparent, var(--silver) 20%, var(--silver) 80%, transparent);
  }
  .front-contact {
    position: absolute;
    top: 400px;
    left: 0; right: 0;
    display: flex;
    align-items: center;
    justify-content: center;
    gap: 18px;
    font-family: "Roboto", Arial, sans-serif;
    font-size: 23px;
    color: var(--white);
  }
  .front-contact__item { display: flex; align-items: center; gap: 12px; }
  .front-contact__divider { width: 1px; height: 28px; background: var(--white); }
  .icon { width: 24px; height: 24px; flex: none; }

  /* Back side */
  .sign--back { background: var(--white); }
  .sign--back .sign__frame-outer { inset: 20px; border: 4px solid var(--orange); }
  .sign--back .sign__frame-inner { inset: 31px; border: 2px solid var(--orange); }
  .back-brand {
    position: absolute;
    top: 62px; left: 0; right: 0;
    display: flex;
    align-items: center;
    justify-content: center;
    gap: 10px;
  }
  .back-brand__dot { width: 40px; height: 40px; border-radius: 50%; background: var(--gray); }
  .back-brand__name { font-weight: 700; font-size: 20px; color: var(--orange-bright); letter-spacing: .5px; }
  .headline {
    position: absolute;
    top: 162px; left: 0; right: 0;
    text-align: center;
    color: var(--navy-ink);
  }
  .headline__main { font-weight: 700; font-size: 41px; line-height: 1.1; }
  .headline__sub { font-weight: 300; font-size: 35px; line-height: 1.2; }
  .service-band {
    position: absolute;
    top: 308px; left: 31px; right: 31px;
    height: 56px;
    background: var(--orange);
    display: flex;
    align-items: center;
    justify-content: center;
    gap: 12px;
    color: var(--white);
    font-weight: 600;
    font-size: 16.5px;
    letter-spacing: .3px;
  }
  .back-contact {
    position: absolute;
    top: 382px; left: 0; right: 0;
    text-align: center;
    color: var(--navy-ink);
  }
  .back-contact__phone {
    display: inline-flex;
    align-items: center;
    gap: 14px;
    font-weight: 700;
    font-size: 38px;
    line-height: 1.1;
  }
  .back-contact__phone .icon { width: 32px; height: 32px; }
  .back-contact__web { font-size: 16px; font-weight: 400; margin-top: 2px; }
</style>
</head>
<body>

  <section class="sign sign--front" aria-label="Sign front side">
    <div class="sign__frame-outer"></div>
    <div class="sign__frame-inner"></div>
    <div class="brand-lockup">
      <span class="brand-lockup__dot"></span>
      <span class="brand-lockup__name">BRACKWELL<br>BUILDERS</span>
    </div>
    <div class="front-rule"></div>
    <div class="front-contact">
      <span class="front-contact__item">
        <svg class="icon" viewBox="0 0 24 24" aria-hidden="true">
          <circle cx="12" cy="12" r="12" fill="#fff"/>
          <path d="M8.2 5.5l2 2.6-1.2 1.6c.8 1.8 2.2 3.3 4.1 4.2l1.6-1.2 2.6 2-1.3 2.3c-4.6-.4-8.8-4.6-9.1-9.2z" fill="#1e1b5a"/>
        </svg>
        810-555-0176
      </span>
      <span class="front-contact__divider"></span>
      <span class="front-contact__item">
        <svg class="icon" viewBox="0 0 24 24" aria-hidden="true" fill="none" stroke="#fff" stroke-width="1.6">
          <circle cx="12" cy="12" r="10"/>
          <ellipse cx="12" cy="12" rx="4.5" ry="10"/>
          <line x1="2" y1="12" x2="22" y2="12"/>
          <line x1="4" y1="7" x2="20" y2="7"/>
          <line x1="4" y1="17" x2="20" y2="17"/>
        </svg>
        brackwellbuilders.com
      </span>
    </div>
  </section>

  <section class="sign sign--back" aria-label="Sign back side">
    <div class="sign__frame-outer"></div>
    <div class="sign__frame-inner"></div>
    <div class="back-brand">
      <span class="back-brand__dot"></span>
      <span class="back-brand__name">BRACKWELL BUILDERS</span>
    </div>
    <div class="headline">
      <div class="headline__main">GENERAL MAINTENANCE</div>
      <div class="headline__sub">FLOORING &amp; REMODELING</div>
    </div>
    <div class="service-band">
      <span>RESIDENTIAL</span><span>|</span><span>COMMERCIAL RENOVATIONS</span><span>|</span><span>MAINTENANCE</span>
    </div>
    <div class="back-contact">
      <div class="back-contact__phone">
        <svg class="icon" viewBox="0 0 24 24" aria-hidden="true">
          <circle cx="12" cy="12" r="12" fill="#1f1d5c"/>
          <path d="M8.2 5.5l2 2.6-1.2 1.6c.8 1.8 2.2 3.3 4.1 4.2l1.6-1.2 2.6 2-1.3 2.3c-4.6-.4-8.8-4.6-9.1-9.2z" fill="#fff"/>
        </svg>
        810-555-0176
      </div>
      <div class="back-contact__web">brackwellbuilders.com</div>
    </div>
  </section>

</body>
</html>
```